Velvet Dice Night Age Verification Landing Page

To create a visually appealing design for the landing page of the adult game "Velvet Dice Night" that confirms the visitor's age.
The design should have a simple and visually appealing look that focuses on two buttons labeled "Yes" and "No". The purpose of the page is to confirm that the visitor is 18 years of age or older before accessing the game's content. Responsive design that works well on desktop and mobile devices. The final output should be delivered in PSD, AI, or Sketch format, along with any necessary images or assets.
I have also attached examples.

```html
<!DOCTYPE html>
<html lang="en">
<head>
<meta charset="UTF-8">
<title>Velvet Dice Night – Age Verification</title>
<link href="https://fonts.googleapis.com/css2?family=Quicksand:wght@500;600;700&display=swap" rel="stylesheet">
<style>
  :root {
    --pink: #d1084f;
    --pink-line: #b0073f;
    --panel: rgba(10, 10, 10, 0.72);
    --white: #ffffff;
    --navy: #1c2a3a;
    --scene-a: #6e6460;
    --scene-b: #8c7d78;
    --scene-c: #4a3d3d;
    --scene-red: #7a1a2a;
  }
  * { margin: 0; padding: 0; box-sizing: border-box; }
  html, body {
    width: 1200px;
    height: 547px;
    overflow: hidden;
    font-family: "Quicksand", sans-serif;
    background: #000;
  }
  .page {
    position: relative;
    width: 1200px;
    height: 547px;
    overflow: hidden;
  }
  .backdrop {
    position: absolute;
    inset: 0;
    background:
      radial-gradient(ellipse 220px 260px at 160px 330px, rgba(190,150,150,0.55), transparent 70%),
      radial-gradient(ellipse 200px 170px at 380px 420px, var(--scene-red), transparent 75%),
      radial-gradient(ellipse 230px 280px at 960px 250px, rgba(200,185,180,0.5), transparent 70%),
      radial-gradient(ellipse 200px 140px at 1120px 340px, rgba(110,20,30,0.6), transparent 75%),
      linear-gradient(90deg, var(--scene-a) 0%, var(--scene-c) 35%, var(--scene-b) 60%, var(--scene-a) 100%);
  }
  .sound-toggle {
    position: absolute;
    left: 1061px;
    top: 19px;
    width: 40px;
    height: 40px;
    background: var(--navy);
    border: 2px solid var(--pink);
    display: flex;
    align-items: center;
    justify-content: center;
  }
  .age-panel {
    position: absolute;
    left: 334px;
    top: 95px;
    width: 532px;
    height: 357px;
    border-radius: 10px;
    background: var(--panel);
  }
  .brand {
    position: absolute;
    left: 0;
    right: 0;
    top: 43px;
    text-align: center;
  }
  .brand-mark {
    display: block;
    margin: 0 auto;
    width: 96px;
    height: 96px;
    border: 1.5px solid var(--pink-line);
    border-radius: 50%;
  }
  .brand-name {
    margin-top: 14px;
    color: var(--pink);
    font-size: 29px;
    font-weight: 700;
    letter-spacing: 1px;
    text-transform: uppercase;
  }
  .question {
    position: absolute;
    left: 0;
    right: 0;
    top: 206px;
    text-align: center;
    color: var(--white);
    font-size: 19px;
    font-weight: 600;
  }
  .choices {
    position: absolute;
    left: 207px;
    top: 245px;
    display: flex;
    gap: 10px;
  }
  .choice {
    width: 54px;
    height: 42px;
    background: var(--pink);
    color: var(--white);
    font-size: 17px;
    font-weight: 600;
    display: flex;
    align-items: center;
    justify-content: center;
  }
  .remember {
    position: absolute;
    left: 209px;
    top: 298px;
    display: flex;
    align-items: center;
    color: var(--white);
    font-size: 12.5px;
    font-weight: 600;
  }
  .remember-box {
    width: 9px;
    height: 9px;
    background: var(--white);
    margin-right: 13px;
  }
</style>
</head>
<body>
  <main class="page">
    <div class="backdrop" role="img" aria-label="Blurred photo of friends relaxing and dancing together in a living room"></div>

    <div class="sound-toggle" aria-label="Toggle music">
      <svg width="22" height="22" viewBox="0 0 24 24" fill="#fff" aria-hidden="true">
        <path d="M9 4 L21 2 V16.5 A3 3 0 1 1 19 13.8 V6.2 L11 7.5 V18.5 A3 3 0 1 1 9 15.8 Z"/>
      </svg>
    </div>

    <section class="age-panel">
      <div class="brand">
        <span class="brand-mark"></span>
        <div class="brand-name">Velvet Dice Night</div>
      </div>
      <p class="question">Are You Over 18 years of Age?</p>
      <div class="choices">
        <div class="choice">Yes</div>
        <div class="choice">No</div>
      </div>
      <div class="remember">
        <span class="remember-box"></span>Remember Me
      </div>
    </section>
  </main>
</body>
</html>
```